DL FLYER - Stroll Sip Nibble Trails

I need a2-sided DL flyer designed to put into Hotel foyers. This will need to stand out as it will be in a rack with multiple other options.

Our tours are all about walking with us to take in great venues for food and beverages with art and history along the way.

We operate in Downtown City plus Harbourside.

I am hoping for the flyer to look something like my website - https://strollsipnibble.example.au/

This website will be updated in the coming weeks with new experiences and a new booking platform.

I want the flyers to be used to drive bookings from the updated website.

Attached are several images that could be used also.

Target Market(s)

Social groups, couples, friends groups & foodies!

Industry/Entity Type

Food & Beverage Walking Tours

Font styles to use
Serif
Sans Serif
Decorative
Script

Colors
0094D4
00A9DD
6FCCEA
C7EBF8
E9F6FB
59FF00
82FF00
B8FF75
E3FFCB
F4FFEA
FFF300
FFF600
FEFA6F
FFFEC7
FFFEE8
F0912C
F2A743
F7CA91
FBE8D2
FDF5EE

Requirements
Must have
• Logo and must look fun. Discount code - GOODVIBES for online price 15% off (not valid on gift voucher purchases)
Nice to have
• similar to my website - colours and styling. I will be updating available tours, costs and timing in the coming weeks. Check out my new booking link to get pricing and tour details - https://www-628q.reservly.example/reservly/b_strollsipnibbletrails_start.html?ctlsrc2=Qm482KTRVA9LZpd7JowsN3hbvY%2F5U8RaxtnBd%2FJqLm%3D&src=02r
Should not have
• .

```html
<!DOCTYPE html>
<html lang="en">
<head>
<meta charset="utf-8">
<title>Stroll Sip Nibble Trails – DL Flyer</title>
<link href="https://fonts.googleapis.com/css2?family=Fredoka:wght@500;600;700&family=Poppins:wght@500;600;700&display=swap" rel="stylesheet">
<style>
  :root{
    --page:#ececec;
    --forest:#263a35;
    --forest-deep:#1d2d29;
    --forest-soft:#3f5a50;
    --mint:#9fd49a;
    --mint-deep:#2f9a62;
    --orange:#ff6a13;
    --cream:#fbf7cf;
    --white:#ffffff;
    --ink:#1e2a27;
  }
  *{box-sizing:border-box;margin:0;padding:0}
  html,body{width:800px;height:1200px;overflow:hidden;background:var(--page)}
  body{position:relative;font-family:"Poppins",sans-serif;color:var(--ink)}

  .flyer{position:absolute;top:195px;width:360px;height:810px;overflow:hidden;background:var(--forest)}
  .flyer--front{left:25px}
  .flyer--back{left:415px}

  .backdrop{position:absolute;inset:0;background:radial-gradient(circle at 30% 25%,var(--forest-soft),var(--forest) 55%,var(--forest-deep))}
  .shape{position:absolute;inset:0;width:360px;height:810px}

  /* front */
  .brand{position:absolute;top:38px;left:0;width:100%;display:flex;align-items:center;justify-content:center;gap:8px}
  .brand-dot{width:34px;height:34px;border-radius:50%;background:var(--orange)}
  .brand-name{font-family:"Poppins",sans-serif;font-weight:600;font-size:17px;color:var(--white)}
  .headline{position:absolute;top:108px;width:100%;text-align:center;font-family:"Fredoka",sans-serif;font-weight:700;font-size:31px;color:var(--white);line-height:1}
  .headline-sub{position:absolute;top:144px;width:100%;text-align:center;font-family:"Fredoka",sans-serif;font-weight:700;font-size:52px;color:var(--mint);letter-spacing:2px;line-height:1}
  .hero-art{position:absolute;left:38px;top:215px;width:284px;height:285px;border-radius:50% 50% 46% 46%;background:radial-gradient(circle at 50% 40%,var(--cream) 0,#f3e8c4 45%,var(--mint) 80%)}
  .intro{position:absolute;top:514px;left:36px;width:288px;text-align:center;font-weight:500;font-size:14px;line-height:18px;color:var(--ink)}
  .divider{position:absolute;top:600px;left:44px;width:272px;height:1px;background:#c9c9c9}
  .divider::after{content:"";position:absolute;left:118px;top:-2px;width:36px;height:5px;border-radius:3px;background:var(--orange)}
  .perks{position:absolute;top:634px;left:25px;width:310px;height:79px;border:1.5px solid var(--orange);border-radius:10px;display:flex}
  .perk{flex:1;position:relative;text-align:center;padding-top:30px;font-family:"Fredoka",sans-serif;font-weight:600;font-size:12.5px;line-height:15px}
  .perk+.perk{border-left:1px solid #d7d7d7}
  .perk-icon{position:absolute;top:-24px;left:50%;margin-left:-22px;width:44px;height:44px;border-radius:50%;background:var(--mint);border:2px solid var(--white);box-shadow:0 0 0 1.5px var(--orange);display:flex;align-items:center;justify-content:center}

  .band{position:absolute;left:0;bottom:0;width:100%;height:67px;background:var(--forest)}
  .phone{position:absolute;top:730px;left:58px;width:244px;height:34px;border-radius:17px;background:var(--orange);display:flex;align-items:center;justify-content:center;gap:6px;font-family:"Fredoka",sans-serif;font-weight:600;font-size:23px;color:var(--white)}
  .phone-icon{width:24px;height:24px;border-radius:50%;background:var(--white);display:flex;align-items:center;justify-content:center}
  .web{position:absolute;top:774px;width:100%;text-align:center;font-family:"Poppins",sans-serif;font-weight:600;font-size:12.5px;letter-spacing:1px;color:var(--white)}

  /* back */
  .section-title{position:absolute;top:28px;width:100%;text-align:center;font-family:"Fredoka",sans-serif;font-weight:700;font-size:22px;color:var(--white)}
  .section-title span{color:var(--orange)}
  .tours{position:absolute;top:70px;left:32px;display:grid;grid-template-columns:141px 141px;grid-template-rows:162px 162px 162px;column-gap:12px;row-gap:11px}
  .tour{position:relative;background:var(--white);border-radius:10px;text-align:center;overflow:hidden}
  .tour-name{height:27px;background:var(--mint);color:var(--white);font-family:"Fredoka",sans-serif;font-weight:600;font-size:9px;line-height:10px;text-transform:uppercase;display:flex;align-items:center;justify-content:center;padding:0 10px}
  .tour-price{font-family:"Fredoka",sans-serif;font-weight:700;font-size:27px;line-height:30px;color:var(--orange);margin-top:2px}
  .tour-time{font-family:"Fredoka",sans-serif;font-weight:600;font-size:10.5px;line-height:13px}
  .tour-place{display:inline-block;width:76px;margin-top:3px;border-radius:7px 7px 0 0;background:var(--orange);color:var(--white);font-family:"Fredoka",sans-serif;font-weight:600;font-size:9px;line-height:13px}
  .tour-photo{display:block;margin:0 auto;width:112px;height:66px;border-radius:8px;border:2px solid var(--white);box-shadow:0 0 0 1px #d0d0d0}
  .photo-food{background:linear-gradient(135deg,#6b4a33,#d9a46a 55%,#efe3cf)}
  .photo-drinks{background:linear-gradient(135deg,#3c3a3a,#a3a7ab 50%,#d98d7a)}
  .photo-friends{background:linear-gradient(135deg,#9e3b2d,#d7a088 50%,#3b4f6a)}
  .photo-dining{background:linear-gradient(135deg,#d9dfe6,#9a7f6a 50%,#3e4a3f)}
  .photo-lunch{background:linear-gradient(135deg,#e3d7c0,#c7824e 50%,#8fa7a8)}
  .photo-guide{background:linear-gradient(135deg,#5a4438,#2a2a2a 50%,#b09080)}

  .offer-lead{position:absolute;top:635px;width:100%;text-align:center;font-family:"Fredoka",sans-serif;font-weight:600;font-size:17px;color:var(--ink)}
  .offer-lead span{color:var(--mint-deep)}
  .offer{position:absolute;top:660px;left:58px;display:flex;align-items:center}
  .offer-pct{font-family:"Fredoka",sans-serif;font-weight:700;font-size:60px;line-height:56px;color:var(--orange);letter-spacing:-2px}
  .offer-off{font-family:"Fredoka",sans-serif;font-weight:600;font-size:20px;align-self:flex-end;margin-left:2px}
  .offer-code{margin-left:10px;padding-left:8px;border-left:1px dashed #888;height:58px}
  .code-label{font-family:"Fredoka",sans-serif;font-weight:600;font-size:12px;color:var(--orange);line-height:15px}
  .code-value{display:inline-block;font-family:"Fredoka",sans-serif;font-weight:700;font-size:17px;line-height:20px;padding:0 4px;margin:2px 0 1px;background:var(--mint);border-radius:4px}
  .code-note{font-size:7px;line-height:8px;font-weight:500;width:110px}
</style>
</head>
<body>

<section class="flyer flyer--front">
  <div class="backdrop" role="img" aria-label="Dimmed photo of diners with drinks and plates on a restaurant table"></div>
  <svg class="shape" viewBox="0 0 360 810" aria-hidden="true">
    <path d="M0 380 C90 350 270 345 360 370 L360 376 C270 356 90 360 0 392 Z" fill="var(--orange)"/>
    <path d="M0 392 C90 362 270 360 360 378 L360 810 L0 810 Z" fill="var(--white)"/>
  </svg>

  <div class="brand">
    <span class="brand-dot"></span>
    <span class="brand-name">Stroll Sip Nibble Trails</span>
  </div>
  <h1 class="headline">Stroll Sip Nibble</h1>
  <div class="headline-sub">TRAILS</div>

  <div class="hero-art" role="img" aria-label="Illustration of a group of walkers in front of a city skyline with a bright sun"></div>

  <p class="intro">Our tours are all about walking with us to take in great venues for food and beverages with art and history along the way.</p>
  <div class="divider"></div>

  <div class="perks">
    <div class="perk">
      <span class="perk-icon"><svg width="18" height="22" viewBox="0 0 18 22"><path d="M9 1C4.6 1 1.5 4.2 1.5 8.3 1.5 13.5 9 21 9 21s7.5-7.5 7.5-12.7C16.5 4.2 13.4 1 9 1z" fill="var(--orange)"/><circle cx="9" cy="8.3" r="2.8" fill="var(--mint)"/></svg></span>
      Explore<br>The City
    </div>
    <div class="perk">
      <span class="perk-icon"><svg width="24" height="20" viewBox="0 0 24 20"><path d="M12 2C6 2 2 5.5 2 9.5c0 2.3 1.3 4.3 3.4 5.6L4.5 19l4.3-2.6c1 .3 2.1.4 3.2.4 6 0 10-3.4 10-7.3S18 2 12 2z" fill="none" stroke="var(--orange)" stroke-width="2"/><circle cx="8" cy="9.5" r="1.4" fill="var(--orange)"/><circle cx="12" cy="9.5" r="1.4" fill="var(--orange)"/><circle cx="16" cy="9.5" r="1.4" fill="var(--orange)"/></svg></span>
      Meet New<br>People
    </div>
    <div class="perk">
      <span class="perk-icon"><svg width="24" height="20" viewBox="0 0 24 20"><path d="M8 2c-1 1.5 1 2.5 0 4M12 1c-1 1.5 1 2.5 0 4M16 2c-1 1.5 1 2.5 0 4" stroke="var(--orange)" stroke-width="1.5" fill="none"/><path d="M2 10h20c0 4.5-4.5 7-10 7S2 14.5 2 10z" fill="none" stroke="var(--orange)" stroke-width="2"/></svg></span>
      Enjoy<br>Great Food
    </div>
  </div>

  <div class="band"></div>
  <div class="phone">
    <span class="phone-icon"><svg width="14" height="14" viewBox="0 0 24 24"><path d="M6.6 10.8c1.4 2.8 3.8 5.1 6.6 6.6l2.2-2.2c.3-.3.7-.4 1-.2 1.1.4 2.3.6 3.6.6.6 0 1 .4 1 1V20c0 .6-.4 1-1 1C10.6 21 3 13.4 3 4c0-.6.4-1 1-1h3.5c.6 0 1 .4 1 1 0 1.3.2 2.5.6 3.6.1.3 0 .7-.2 1l-2.3 2.2z" fill="var(--forest)"/></svg></span>
    +61 400 555 018
  </div>
  <div class="web">www.strollsipnibble.example.au</div>
</section>

<section class="flyer flyer--back">
  <div class="backdrop" role="img" aria-label="Dimmed photo of a busy bar with guests enjoying drinks"></div>
  <h2 class="section-title">TOURS <span>&amp; EXPERIENCES</span></h2>

  <div class="tours">
    <article class="tour">
      <div class="tour-name">Grill &amp; Ale<br>Stroll</div>
      <div class="tour-price">$89</div>
      <div class="tour-time">1:00 PM - 4:30 PM</div>
      <span class="tour-place">Downtown</span>
      <div class="tour-photo photo-food" role="img" aria-label="Plated grilled dish on a wooden table"></div>
    </article>
    <article class="tour">
      <div class="tour-name">Sunset Supper<br>Wander</div>
      <div class="tour-price">$96</div>
      <div class="tour-time">4:30 PM - 8:30 PM</div>
      <span class="tour-place">Downtown</span>
      <div class="tour-photo photo-drinks" role="img" aria-label="Wine being poured beside an ice bucket"></div>
    </article>
    <article class="tour">
      <div class="tour-name">Sunday Harbour<br>Sips</div>
      <div class="tour-price">$94</div>
      <div class="tour-time">2:30 PM - 6:30 PM</div>
      <span class="tour-place">Harbourside</span>
      <div class="tour-photo photo-friends" role="img" aria-label="Friends raising glasses at a table"></div>
    </article>
    <article class="tour">
      <div class="tour-name">Midweek<br>Street Eats</div>
      <div class="tour-price">$72</div>
      <div class="tour-time">5:30 PM - 8:30 PM</div>
      <span class="tour-place">Harbourside</span>
      <div class="tour-photo photo-dining" role="img" aria-label="Guests sharing dishes at a long dining table"></div>
    </article>
    <article class="tour">
      <div class="tour-name">Laneway<br>Lunch Loop</div>
      <div class="tour-price">$86</div>
      <div class="tour-time">11:30 AM - 3:00 PM</div>
      <span class="tour-place">Downtown</span>
      <div class="tour-photo photo-lunch" role="img" aria-label="Bowls of dumplings and salad on a table"></div>
    </article>
    <article class="tour">
      <div class="tour-name">Cosy Cellar<br>Crawl</div>
      <div class="tour-price">$92</div>
      <div class="tour-time">12:00 PM - 3:00 PM</div>
      <span class="tour-place">Downtown</span>
      <div class="tour-photo photo-guide" role="img" aria-label="Tour guide talking with a group in a cosy venue"></div>
    </article>
  </div>

  <svg class="shape" viewBox="0 0 360 810" aria-hidden="true">
    <path d="M0 668 C60 615 190 585 320 598 L360 606 L360 618 C220 600 100 612 0 692 Z" fill="var(--orange)"/>
    <path d="M0 692 C100 614 220 602 360 618 L360 810 L0 810 Z" fill="var(--white)"/>
  </svg>

  <div class="offer-lead"><span>BOOK ONLINE</span> TO GET</div>
  <div class="offer">
    <span class="offer-pct">15%</span>
    <span class="offer-off">OFF</span>
    <div class="offer-code">
      <div class="code-label">DISCOUNT CODE</div>
      <div class="code-value">GOODVIBES</div>
      <div class="code-note">(not valid on gift voucher purchases)</div>
    </div>
  </div>

  <div class="band"></div>
  <div class="phone">
    <span class="phone-icon"><svg width="14" height="14" viewBox="0 0 24 24"><path d="M6.6 10.8c1.4 2.8 3.8 5.1 6.6 6.6l2.2-2.2c.3-.3.7-.4 1-.2 1.1.4 2.3.6 3.6.6.6 0 1 .4 1 1V20c0 .6-.4 1-1 1C10.6 21 3 13.4 3 4c0-.6.4-1 1-1h3.5c.6 0 1 .4 1 1 0 1.3.2 2.5.6 3.6.1.3 0 .7-.2 1l-2.3 2.2z" fill="var(--forest)"/></svg></span>
    +61 400 555 018
  </div>
  <div class="web">www.strollsipnibble.example.au</div>
</section>

</body>
</html>
```